Business card for Eyelash extension salon in Crestview Hills,California USA

We need new business card for our salon in Crestview Hills. The salon name is 'Lashvera' . We would like to have...Business name: Lashvera Name of person: will provide later Address 4720 N.Alder Crest Ave Crestview Hills , CA 90210 Phone: will provide later (Text only) Web: www.lashverastudio.example Snapgrid icon, Circlebook icon follow us for seasonal campaign and news @lashverastudiolounge Design should look elegant, high-end, clean, simple, cohesive with my brand. Please refer my brand board. Business name color will be metallic bronzy color. Im thinking grey background or white background. Thanks

Target Market(s)

25-35. Gender neutral. People who are in Entertainment business industry.
This is High-end Eyelash extension salon in Crestview Hills

Industry/Entity Type

Beauty Salon

Contact Information for Business Card

Business name: Lashvera
Name of person: will provide later
Address 4720 N.Alder Crest Ave Crestview Hills , CA 90210
Phone: will provide later (Text only)
Web: www.lashverastudio.example
Snapgrid icon, Circlebook icon
follow us for seasonal campaign and news @lashverastudiolounge

Requirements
Must have
• Beautiful, elegant, clean and simple look but very attractive and modern
Should not have
• We don't like too clutter, too busy designs.

```html
<!DOCTYPE html>
<html lang="en">
<head>
<meta charset="utf-8">
<title>Lashvera Business Card</title>
<link href="https://fonts.googleapis.com/css2?family=Cormorant+Garamond:wght@500;600;700&family=Montserrat:wght@500&display=swap" rel="stylesheet">
<style>
  :root {
    --page: #e6e6e6;
    --white-frame: #f6f6f6;
    --bronze: #8b6447;
    --band: #8a6a52;
    --ink: #3c3a38;
    --muted: #a9a7a5;
    --paper: #ffffff;
  }
  * { margin: 0; padding: 0; box-sizing: border-box; }
  html, body { width: 1200px; height: 960px; overflow: hidden; }
  body {
    background: var(--page);
    position: relative;
    font-family: "Cormorant Garamond", Georgia, serif;
    color: var(--ink);
  }
  .card {
    position: absolute;
    width: 600px;
    height: 342px;
    box-shadow: 2px 3px 4px rgba(0,0,0,0.25);
  }
  .card--front { left: 302px; top: 123px; background: linear-gradient(135deg, #f4f4f4, #dcdcdc 50%, #f6f6f6); }
  .card--back { left: 299px; top: 495px; height: 343px; background: var(--white-frame); }

  .marble {
    position: absolute;
    left: 14px; top: 13px;
    width: 571px; height: 313px;
    background:
      radial-gradient(ellipse at 20% 20%, rgba(170,170,170,0.35), transparent 45%),
      radial-gradient(ellipse at 85% 85%, rgba(160,160,160,0.4), transparent 45%),
      radial-gradient(ellipse at 70% 15%, rgba(185,185,185,0.3), transparent 40%),
      linear-gradient(160deg, #ececec, #f7f7f7 45%, #e4e4e4);
  }
  .brand {
    position: absolute;
    left: 70px; top: 122px;
    width: 240px;
    text-align: center;
  }
  .brand__name {
    font-size: 66px;
    font-weight: 500;
    color: var(--bronze);
    line-height: 1;
    letter-spacing: 1px;
  }
  .brand__place {
    margin-top: 26px;
    padding-left: 90px;
    font-family: "Montserrat", Arial, sans-serif;
    font-size: 7.5px;
    letter-spacing: 1.5px;
    color: var(--bronze);
  }
  .contact {
    position: absolute;
    left: 339px; top: 93px;
    font-size: 15px;
    line-height: 18px;
  }
  .contact__name {
    font-size: 23px;
    font-weight: 700;
    color: var(--bronze);
    letter-spacing: 0.5px;
    line-height: 22px;
  }
  .contact__title {
    font-size: 16px;
    font-weight: 600;
    color: var(--muted);
    line-height: 18px;
  }
  .contact__address { margin-top: 8px; font-weight: 500; }
  .contact__list { list-style: none; margin-top: 8px; font-weight: 500; }
  .contact__list li { display: flex; align-items: center; gap: 8px; height: 19px; }
  .contact__list svg { width: 12px; height: 12px; fill: var(--bronze); flex: none; }

  .photo { position: absolute; top: 15px; }
  .photo--plants {
    left: 17px; width: 176px; height: 265px;
    background: linear-gradient(180deg, #eef0ef, #dfe4df 55%, #cfd8cc);
  }
  .photo--room {
    left: 194px; width: 391px; height: 311px;
    background: linear-gradient(180deg, #e9e8e6 0%, #d9d7d4 45%, #8f7a68 75%, #a6a4a2 100%);
  }
  .band {
    position: absolute;
    left: 17px; top: 280px;
    width: 176px; height: 46px;
    background: var(--band);
    color: var(--paper);
  }
  .band__brand {
    position: absolute;
    left: 8px; top: 10px;
    font-size: 16px;
    font-weight: 500;
    line-height: 1;
  }
  .band__brand small {
    display: block;
    font-family: "Montserrat", Arial, sans-serif;
    font-size: 4px;
    letter-spacing: 1px;
    margin-top: 3px;
    padding-left: 10px;
  }
  .band__social {
    position: absolute;
    right: 8px; top: 10px;
    list-style: none;
    font-size: 10px;
    font-weight: 600;
    line-height: 13px;
    text-align: right;
  }
</style>
</head>
<body>

<section class="card card--front" aria-label="Business card front">
  <div class="marble" role="img" aria-label="White marble texture background"></div>
  <div class="brand">
    <div class="brand__name">Lashvera</div>
    <div class="brand__place">CRESTVIEW HILLS</div>
  </div>
  <div class="contact">
    <div class="contact__name">AVERY LANE</div>
    <div class="contact__title">CEO/FOUNDER</div>
    <div class="contact__address">4720 N.Alder Crest Ave<br>Crestview Hills, CA 90099</div>
    <ul class="contact__list">
      <li>
        <svg viewBox="0 0 24 24" aria-hidden="true"><path d="M6.6 10.8a15 15 0 0 0 6.6 6.6l2.2-2.2c.3-.3.7-.4 1-.2 1.1.4 2.3.6 3.6.6.6 0 1 .4 1 1V20c0 .6-.4 1-1 1A17 17 0 0 1 3 4c0-.6.4-1 1-1h3.5c.6 0 1 .4 1 1 0 1.3.2 2.5.6 3.6.1.3 0 .7-.2 1z"/></svg>
        555 010 2468
      </li>
      <li>
        <svg viewBox="0 0 24 24" aria-hidden="true"><path d="M2 5h20v14H2z"/><path d="M3 6l9 6 9-6v-.5H3z" fill="#fff"/></svg>
        news@lashverastudio.example
      </li>
      <li>
        <svg viewBox="0 0 24 24" aria-hidden="true"><circle cx="12" cy="12" r="10"/><path d="M2 12h20M12 2c3 3 3 17 0 20M12 2c-3 3-3 17 0 20" stroke="#fff" stroke-width="1.5" fill="none"/></svg>
        lashverastudio.example
      </li>
    </ul>
  </div>
</section>

<section class="card card--back" aria-label="Business card back">
  <div class="photo photo--plants" role="img" aria-label="Photo of hanging macrame plant holders by a bright window"></div>
  <div class="photo photo--room" role="img" aria-label="Photo of a bright salon lounge with white armchairs, fireplace and wooden table"></div>
  <div class="band">
    <div class="band__brand">Lashvera<small>CRESTVIEW HILLS</small></div>
    <ul class="band__social">
      <li>Circlebook</li>
      <li>Snapgrid</li>
    </ul>
  </div>
</section>

</body>
</html>
```